Lantern Orchard Reverie Event Flyer - Fundraiser for a Civic Assembly Candidate

Working on an event flyer for a fundraiser for a Verdantist candidate for Assembly in Tennessee. Hosting an event for him that's a Lantern Orchard Reverie theme, and I need a cool flyer that fits the theme with event details.
Host names will be added to the flyer on an ongoing basis, so will need someone who can quickly add names to flyer as hosts commit. Would like to agree to a fee for all work up front.
I'm attaching a mockup of a flyer that my friend did, before he had to back out because of work commitments, as well as a couple of pieces of Lantern Orchard Reverie art that I think are cool.
Verdantist

```html
<!DOCTYPE html>
<html lang="en">
<head>
<meta charset="utf-8">
<title>A Lantern Orchard Reverie Civic Meeting Eve – Reception for Jonah Merrick</title>
<link href="https://fonts.googleapis.com/css2?family=Great+Vibes&family=Italianno&family=Open+Sans:wght@400;600;700&display=swap" rel="stylesheet">
<style>
  :root {
    --night: #0d1220;
    --night-deep: #070a12;
    --glow: #e9e2c9;
    --ink: #ffffff;
    --ice: #cfe6f7;
    --soft: #eef0f2;
  }
  html, body {
    margin: 0;
    padding: 0;
    width: 848px;
    height: 1200px;
    overflow: hidden;
    background: var(--night-deep);
  }
  .flyer {
    position: relative;
    width: 848px;
    height: 1200px;
    overflow: hidden;
    color: var(--ink);
    font-family: "Open Sans", Arial, sans-serif;
  }
  .scene {
    position: absolute;
    inset: 0;
    background:
      radial-gradient(ellipse 340px 260px at 300px 640px, rgba(233,226,201,0.85), rgba(185,180,162,0.45) 45%, rgba(44,60,92,0) 100%),
      linear-gradient(90deg, #1a2a4a 0px, #2a3d63 60px, #1c2a44 130px, rgba(20,28,46,0) 160px),
      linear-gradient(180deg, #141a26 0%, #2c3442 30%, #4a5262 50%, #2a3040 68%, #141820 82%, var(--night-deep) 100%);
  }
  .title-group { margin: 0; font-weight: 400; }
  .text-block {
    position: absolute;
    left: 0;
    width: 100%;
    text-align: center;
    margin: 0;
    white-space: nowrap;
    text-shadow: 0 2px 6px rgba(0,0,0,0.55);
  }
  .invited {
    top: 14px;
    font-family: "Italianno", cursive;
    font-size: 58px;
    line-height: 1;
  }
  .title {
    font-family: "Great Vibes", cursive;
    font-weight: 400;
    line-height: 1;
  }
  .title-a { top: 92px; font-size: 150px; left: -40px; }
  .title-lantern { top: 220px; font-size: 96px; }
  .title-meet { top: 330px; font-size: 120px; left: 10px; }
  .title-meet .civic { color: var(--ice); }
  .title-eve { top: 432px; font-size: 92px; left: 150px; }
  .details {
    font-family: "Italianno", cursive;
    font-size: 52px;
    line-height: 1;
    letter-spacing: 1px;
  }
  .reception { top: 568px; }
  .date { top: 612px; }
  .date sup { font-size: 28px; }
  .home { top: 700px; }
  .address { top: 748px; font-size: 50px; }
  .contribution {
    top: 850px;
    font-size: 17px;
    line-height: 32px;
  }
  .rsvp {
    top: 944px;
    font-size: 17px;
    line-height: 28px;
  }
  .rsvp .or {
    font-family: "Italianno", cursive;
    font-size: 26px;
    position: relative;
    top: 10px;
  }
  .paid-for {
    position: absolute;
    left: 200px;
    top: 1047px;
    width: 448px;
    height: 37px;
    border: 1.5px solid var(--soft);
    box-sizing: border-box;
    display: flex;
    align-items: center;
    justify-content: center;
    font-size: 16px;
    font-variant: small-caps;
    letter-spacing: 2px;
  }
  .campaign-name {
    position: absolute;
    left: 0;
    width: 100%;
    top: 1110px;
    display: flex;
    align-items: center;
    justify-content: center;
    gap: 10px;
    font-weight: 700;
    font-size: 26px;
    letter-spacing: 1px;
    text-transform: uppercase;
  }
  .campaign-name .mark {
    width: 14px;
    height: 14px;
    background: var(--ink);
  }
</style>
</head>
<body>
  <main class="flyer">
    <div class="scene" role="img" aria-label="Moonlit orchard meadow beneath a starry night sky, framed by a large tree trunk and glowing lantern-lit branches"></div>

    <p class="text-block invited">You're Cordially Invited to</p>

    <h1 class="title-group">
      <span class="text-block title title-a">A</span>
      <span class="text-block title title-lantern">Lantern Orchard's</span>
      <span class="text-block title title-meet"><span class="civic">Civic</span>Meeting</span>
      <span class="text-block title title-eve">Eve</span>
    </h1>

    <p class="text-block details reception">Reception for Jonah Merrick</p>
    <p class="text-block details date">Wednesday, August 23<sup>rd</sup> 6<sup>00</sup>-9<sup>00</sup>pm</p>
    <p class="text-block details home">Home of Walter Brisby</p>
    <p class="text-block details address">418B Linden Row, Nashville, TN 37216</p>

    <p class="text-block contribution">Suggested Contribution:<br>$20.18 Friend | $100 Supporter | $250 Host</p>

    <p class="text-block rsvp">RSVP at www.JonahMerrick.com/Reverie<span class="or">or</span><br>RSVP by Email at RSVP@JonahMerrick.com</p>

    <div class="paid-for">Paid for by Merrick for Civic Assembly</div>

    <div class="campaign-name"><span class="mark"></span>Jonah Merrick</div>
  </main>
</body>
</html>
```